Create a business promotion flyer to leave in customer mailboxes. We are a bulk petroleum supplier, servicing any industry that requires diesel. Base in griffith NSW, servicing griffith area and surrounds.

Business Name - Terra Diesel
Fuel@terradiesel-example.com.au
Owen - 0491 570 362 ohartley@terradiesel-example.com.au
Liam - 0491 570 718 lprosser@terradiesel-example.com.au
Simon - 0491 570 905 skenway@terradiesel-example.com.au
Office 02 5550 1734

Bulk Fuel deliveries.
Oils & lubricants
Local Family owned business

```html
<!DOCTYPE html>
<html lang="en">
<head>
<meta charset="utf-8">
<title>Terra Diesel – Bulk Fuel Flyer</title>
<link rel="stylesheet" href="https://fonts.googleapis.com/css2?family=Inter:wght@400;500;600&display=swap">
<style>
:root{
  --red:#e0162b;
  --red-deep:#9e1322;
  --ink:#1c1c1e;
  --black:#050505;
  --white:#ffffff;
  --grey:#d9d9d9;
}
*{margin:0;padding:0;box-sizing:border-box}
html,body{width:1200px;height:862px;overflow:hidden;background:var(--white);font-family:'Inter',sans-serif;color:var(--white)}
.canvas{position:relative;width:1200px;height:862px}
.page{position:absolute;top:71px;width:524px;height:741px;overflow:hidden;
  background:linear-gradient(180deg,#222224 0%,#17171a 60%,#0c0c0d 100%)}
.page--front{left:52px}
.page--back{left:611px}
.page .base{position:absolute;left:0;right:0;top:655px;bottom:0;background:var(--black)}
.abs{position:absolute}
.photo{position:absolute;left:0;top:0;width:524px}
.photo--depot{height:300px;background:linear-gradient(180deg,#6d93c9 0%,#b9c9dc 35%,#c8cacc 60%,#9a9a98 100%)}
.photo--nozzle{height:260px;background:linear-gradient(135deg,#3a0d10 0%,#5a1a1c 45%,#2a0a0c 100%)}
.shapes{position:absolute;left:0;top:0}
.brand-badge{position:absolute;width:106px;height:106px;border-radius:50%;background:var(--black);
  box-shadow:3px 3px 0 #555;display:flex;align-items:center;justify-content:center;text-align:center}
.brand-badge span{color:var(--red);font-weight:600;font-size:15px;line-height:1.1}
.headline{position:absolute;left:34px;font-size:21px;font-weight:500;line-height:30px;letter-spacing:.2px}
.headline .hl{color:var(--red)}
.tagline{position:absolute;left:34px;top:384px;font-size:12px}
.checklist{position:absolute;left:34px;top:425px;width:132px;height:155px;border:1px solid #444;background:#0d0d0e;list-style:none;padding:11px 0 0 9px}
.checklist li{font-size:9px;height:23px;display:flex;align-items:center;gap:4px}
.checklist svg{flex:none}
.intro{position:absolute;left:192px;top:430px;width:300px}
.intro h3{color:var(--red);font-size:12px;font-weight:500;margin-bottom:8px}
.intro p{font-size:8px;line-height:12.4px}
.sector-band{position:absolute;left:192px;top:550px;width:332px;height:46px;background:linear-gradient(90deg,#7a1520,#3a1014)}
.sector-tag{position:absolute;left:200px;top:543px;padding:3px 6px;background:var(--black);font-size:6px}
.sectors{position:absolute;left:200px;top:562px;font-size:9px;line-height:15px}
.cta{position:absolute;left:34px;top:621px;width:455px;height:91px;background:linear-gradient(90deg,#a81424,#7c111c);text-align:center}
.cta h4{font-size:14px;font-weight:500;margin-top:19px;letter-spacing:.3px}
.cta p{font-size:8.5px;margin-top:9px}
.cta .mail{font-size:13px;margin-top:8px}
.footer{position:absolute;top:722px;left:31px;right:34px;display:flex;justify-content:space-between;font-size:9px}
.footer .ico{display:inline-block;width:7px;height:7px;margin-right:3px;vertical-align:-1px}
.back-title{position:absolute;left:27px;top:87px;font-size:21px;font-weight:500;line-height:30px}
.back-title .hl{color:var(--red)}
.row{position:absolute;display:flex;gap:10px}
.avatar{width:44px;height:44px;border-radius:50%;background:radial-gradient(circle at 50% 40%,#8a6a56,#3a3a3c);flex:none}
.icon-disc{width:44px;height:44px;border-radius:50%;background:var(--grey);flex:none;display:flex;align-items:center;justify-content:center}
.row h5{color:var(--red);font-size:11px;font-weight:500;margin:1px 0 6px}
.row ul{list-style:none;font-size:7px;line-height:10.5px}
.row ul li::before{content:"•";margin-right:4px}
.row p{font-size:7px;line-height:11px;width:170px}
.divider{position:absolute;left:43px;top:510px;width:438px;border-top:1px dashed #aaa}
.why{position:absolute;left:0;width:524px;top:531px;text-align:center;font-size:17px;font-weight:500}
.why-list{position:absolute;top:574px;font-size:11px}
</style>
</head>
<body>
<div class="canvas">

  <section class="page page--front">
    <div class="base"></div>
    <div class="photo photo--depot" role="img" aria-label="Photo of a white road train fuel tanker parked in front of a depot shed under a blue cloudy sky"></div>
    <svg class="shapes" width="524" height="400" viewBox="0 0 524 400">
      <polygon points="0,283 412,232 524,280 524,400 0,400" fill="#b3111f"/>
      <polygon points="0,302 412,246 524,300 524,400 0,400" fill="#1f1f21"/>
      <polygon points="0,283 412,232 524,280 524,285 412,238 0,291" fill="var(--red)"/>
    </svg>
    <div class="brand-badge" style="left:289px;top:177px"><span>Terra<br>Diesel</span></div>

    <h1 class="headline" style="top:311px"><span class="hl">RELIABLE BULK FUEL</span> DELIVERY ACROSS<br>GRIFFITH &amp; SURROUNDING AREAS</h1>
    <p class="tagline">Keeping Farms, Transport, Construction &amp; Industry Moving</p>

    <ul class="checklist">
      <li><svg width="7" height="6" viewBox="0 0 7 6"><path d="M1 3l2 2 3-4" stroke="#fff" fill="none"/></svg>Bulk Diesel Deliveries</li>
      <li><svg width="7" height="6" viewBox="0 0 7 6"><path d="M1 3l2 2 3-4" stroke="#fff" fill="none"/></svg>Oils &amp; Lubricants</li>
      <li><svg width="7" height="6" viewBox="0 0 7 6"><path d="M1 3l2 2 3-4" stroke="#fff" fill="none"/></svg>Fast Local Service</li>
      <li><svg width="7" height="6" viewBox="0 0 7 6"><path d="M1 3l2 2 3-4" stroke="#fff" fill="none"/></svg>Competitive Pricing</li>
      <li><svg width="7" height="6" viewBox="0 0 7 6"><path d="M1 3l2 2 3-4" stroke="#fff" fill="none"/></svg>Family-Owned Business</li>
      <li><svg width="7" height="6" viewBox="0 0 7 6"><path d="M1 3l2 2 3-4" stroke="#fff" fill="none"/></svg>Trusted Local Supplier</li>
    </ul>

    <div class="intro">
      <h3>Fuel Delivered When You Need It</h3>
      <p>Based in Griffith, NSW, Terra Diesel proudly services local farms, transport operators, construction companies, earthmoving contractors, commercial businesses, and industrial operations with dependable fuel supply solutions. Whether you require scheduled deliveries or urgent fuel supply, our experienced team is ready to help keep your operation running efficiently.</p>
    </div>

    <div class="sector-band"></div>
    <div class="sector-tag">SERVICING</div>
    <p class="sectors">Agriculture • Transport • Construction • Mining Support •<br>Earthmoving • Commercial Operations • Industrial Sites</p>

    <div class="cta">
      <h4>CALL TODAY FOR BULK FUEL DELIVERY</h4>
      <p>Fast, reliable diesel supply across Griffith &amp; surrounds</p>
      <p class="mail">Fuel@terradiesel-example.com.au</p>
    </div>
    <div class="footer">
      <span><svg class="ico" viewBox="0 0 8 8"><rect x="0" y="1" width="8" height="7" rx="1" fill="var(--red)"/></svg>Office: 02 5550 1734</span>
      <span><svg class="ico" viewBox="0 0 8 8"><path d="M1 1l2 0 1 2-1 1c1 1 1 1 2 2l1-1 2 1v2C4 8 0 4 1 1z" fill="#888"/></svg>Contact us today for competitive pricing</span>
    </div>
  </section>

  <section class="page page--back">
    <div class="base"></div>
    <div class="photo photo--nozzle" role="img" aria-label="Dark red toned close-up photo of a hand holding a diesel fuel nozzle"></div>
    <svg class="shapes" width="524" height="300" viewBox="0 0 524 300">
      <polygon points="0,247 413,176 524,243 524,300 0,300" fill="var(--red)"/>
      <polygon points="0,256 413,186 524,256 524,300 0,300" fill="#1f1f21"/>
    </svg>
    <h2 class="back-title"><span class="hl">YOUR LOCAL BULK</span><br>FUEL SPECIALISTS</h2>
    <div class="brand-badge" style="left:342px;top:34px"><span>Terra<br>Diesel</span></div>

    <div class="row" style="left:42px;top:285px">
      <div class="avatar" role="img" aria-label="Portrait photo of Owen Hartley"></div>
      <div><h5>OWEN HARTLEY</h5><ul><li>0491 570 362</li><li>ohartley@terradiesel-example.com.au</li></ul></div>
    </div>
    <div class="row" style="left:42px;top:359px">
      <div class="avatar" role="img" aria-label="Portrait photo of Liam Prosser"></div>
      <div><h5>LIAM PROSSER</h5><ul><li>0491 570 718</li><li>lprosser@terradiesel-example.com.au</li></ul></div>
    </div>
    <div class="row" style="left:42px;top:433px">
      <div class="avatar" role="img" aria-label="Portrait photo of Simon Kenway"></div>
      <div><h5>SIMON KENWAY</h5><ul><li>0491 570 905</li><li>skenway@terradiesel-example.com.au</li></ul></div>
    </div>

    <div class="row" style="left:271px;top:285px">
      <div class="icon-disc"><svg width="26" height="18" viewBox="0 0 26 18" fill="none" stroke="#333" stroke-width="1.2"><rect x="1" y="3" width="15" height="9" rx="3"/><path d="M16 6h5l3 4v3H16z"/><circle cx="5" cy="15" r="2"/><circle cx="11" cy="15" r="2"/><circle cx="20" cy="15" r="2"/></svg></div>
      <div><h5>BULK FUEL DELIVERIES</h5><p>Reliable diesel supply delivered directly to your site, farm, depot, workshop, or storage facility.</p></div>
    </div>
    <div class="row" style="left:271px;top:359px">
      <div class="icon-disc"><svg width="22" height="22" viewBox="0 0 22 22" fill="none" stroke="#333" stroke-width="1.2"><path d="M3 9a8 6 0 0 1 16 0"/><rect x="2" y="9" width="18" height="11"/><path d="M2 13h18M2 17h18M7 9v11M15 9v11"/></svg></div>
      <div><h5>OILS &amp; LUBRICANTS</h5><p>Quality oils and lubricants for agricultural equipment, heavy machinery, transport fleets, and commercial vehicles.</p></div>
    </div>
    <div class="row" style="left:271px;top:433px">
      <div class="icon-disc"><svg width="24" height="22" viewBox="0 0 24 22" fill="none" stroke="#333" stroke-width="1.2"><rect x="1" y="3" width="18" height="15"/><path d="M5 1v4M10 1v4M15 1v4M4 8h3v3H4zM9 8h3v3H9zM4 13h3v3H4z"/><circle cx="18" cy="16" r="5" fill="#d9d9d9"/><path d="M18 13v3h2"/></svg></div>
      <div><h5>SCHEDULED DELIVERIES</h5><p>Custom fuel management solutions designed around your operational requirements.</p></div>
    </div>

    <div class="divider"></div>
    <h3 class="why">WHY CHOOSE TERRA DIESEL?</h3>
    <span class="why-list" style="left:47px">100% Reliable Delivery</span>
    <span class="why-list" style="left:200px">Competitive Pricing</span>
    <span class="why-list" style="left:339px">Proudly Family-Owned</span>

    <div class="cta">
      <h4>CALL TODAY FOR BULK FUEL DELIVERY</h4>
      <p>Fast, reliable diesel supply across Griffith &amp; surrounds</p>
      <p class="mail">Fuel@terradiesel-example.com.au</p>
    </div>
    <div class="footer">
      <span><svg class="ico" viewBox="0 0 8 8"><rect x="0" y="1" width="8" height="7" rx="1" fill="var(--red)"/></svg>Office: 02 5550 1734</span>
      <span><svg class="ico" viewBox="0 0 8 8"><path d="M1 1l2 0 1 2-1 1c1 1 1 1 2 2l1-1 2 1v2C4 8 0 4 1 1z" fill="#888"/></svg>Contact us today for competitive pricing</span>
    </div>
  </section>

</div>
</body>
</html>
```